Business card for a new cabinet shop company named Veloran Cabinets for high end cabinets

Design a business card, thinking dark rich green with colours to speak of high end luxury ie; cream, gold, black possibly

Mitchell Tarrowby
Director Craftsman
Email: info@veloranjoinery-example.com.au
Instagram : @veloran.cabinets

```html
<!DOCTYPE html>
<html lang="en">
<head>
<meta charset="utf-8">
<title>Veloran Cabinets — Business Card</title>
<link rel="stylesheet" href="https://fonts.googleapis.com/css2?family=Arimo:wght@400;700&display=swap">
<style>
  :root {
    --backdrop: #e4e4e4;
    --card-white: #ffffff;
    --green-top: #1f3d30;
    --green-bottom: #142a20;
    --green-rich: #183528;
    --gold: #c9a95c;
    --text-grey: #555555;
    --muted-grey: #6b6b6b;
    --rule: #b5b5b5;
    --deboss: #2e5444;
  }
  * { box-sizing: border-box; margin: 0; padding: 0; }
  html, body { width: 1200px; height: 1200px; overflow: hidden; }
  body {
    background: var(--backdrop);
    font-family: "Arimo", Arial, sans-serif;
    position: relative;
  }
  .card {
    position: absolute;
    left: 256px;
    width: 688px;
    height: 394px;
    border-radius: 20px;
    overflow: hidden;
  }
  .card--front { top: 150px; background: var(--card-white); }
  .card--back {
    top: 656px;
    background: linear-gradient(180deg, var(--green-top), var(--green-bottom));
  }

  /* Front */
  .brand {
    position: absolute;
    left: 62px;
    top: 168px;
    display: flex;
    align-items: center;
    gap: 14px;
  }
  .brand__mark {
    width: 20px;
    height: 20px;
    background: var(--green-rich);
  }
  .brand__name {
    font-size: 27px;
    font-weight: 400;
    color: var(--gold);
    letter-spacing: 0.5px;
    white-space: nowrap;
  }
  .divider {
    position: absolute;
    left: 343px;
    top: 124px;
    width: 1px;
    height: 140px;
    background: var(--rule);
  }
  .contact-block {
    position: absolute;
    left: 370px;
    top: 124px;
  }
  .person__name {
    font-size: 27px;
    font-weight: 700;
    color: var(--gold);
    line-height: 1.1;
    white-space: nowrap;
  }
  .person__role {
    font-size: 15px;
    color: var(--muted-grey);
    margin-top: 4px;
  }
  .contacts {
    list-style: none;
    margin-top: 22px;
  }
  .contacts li {
    display: flex;
    align-items: center;
    gap: 10px;
    font-size: 16px;
    color: var(--text-grey);
    height: 20px;
    white-space: nowrap;
  }
  .contacts svg { width: 15px; height: 15px; flex: none; }
  .band {
    position: absolute;
    left: 0; right: 0; bottom: 0;
    height: 16px;
    display: flex;
  }
  .band__gold { width: 419px; background: var(--gold); }
  .band__gap { width: 4px; background: var(--card-white); }
  .band__green { flex: 1; background: var(--green-rich); }

  /* Back */
  .brand--large {
    position: absolute;
    left: 0; right: 0;
    top: 0; bottom: 0;
    display: flex;
    align-items: center;
    justify-content: center;
    gap: 26px;
  }
  .brand--large .brand__mark {
    width: 40px;
    height: 40px;
    background: var(--deboss);
  }
  .brand--large .brand__name {
    font-size: 56px;
    color: var(--deboss);
    letter-spacing: 1px;
  }
</style>
</head>
<body>

<section class="card card--front" aria-label="Business card front">
  <div class="brand">
    <span class="brand__mark" aria-hidden="true"></span>
    <span class="brand__name">Veloran Cabinets</span>
  </div>

  <div class="divider"></div>

  <div class="contact-block">
    <h1 class="person__name">Mitchell Tarrowby</h1>
    <p class="person__role">Director Craftsman</p>
    <ul class="contacts">
      <li>
        <svg viewBox="0 0 16 16" aria-hidden="true">
          <rect x="1.5" y="3.5" width="13" height="9" fill="var(--gold)"/>
          <path d="M1.5 3.5 L8 9 L14.5 3.5" fill="none" stroke="#fff" stroke-width="1.2"/>
        </svg>
        info@veloranjoinery-example.com.au
      </li>
      <li>
        <svg viewBox="0 0 16 16" aria-hidden="true">
          <circle cx="8" cy="8" r="6.5" fill="var(--gold)"/>
          <path d="M1.5 8 H14.5 M8 1.5 C5 5 5 11 8 14.5 M8 1.5 C11 5 11 11 8 14.5" fill="none" stroke="#fff" stroke-width="1"/>
        </svg>
        www.veloranjoinery-example.com.au
      </li>
      <li>
        <svg viewBox="0 0 16 16" aria-hidden="true">
          <circle cx="8" cy="8" r="6.5" fill="var(--gold)"/>
        </svg>
        @veloran.cabinets
      </li>
    </ul>
  </div>

  <div class="band" aria-hidden="true">
    <span class="band__gold"></span>
    <span class="band__gap"></span>
    <span class="band__green"></span>
  </div>
</section>

<section class="card card--back" aria-label="Business card back">
  <div class="brand brand--large">
    <span class="brand__mark" aria-hidden="true"></span>
    <span class="brand__name">Veloran Cabinets</span>
  </div>
</section>

</body>
</html>
```